Poster & Flyer - Golf Tournament

Poster and Flyer (2 sperapate) is required for an upcoming Torvenne Classic Golf Tournament. Although this tournament is amongst friends only (normally 40 people) we want to announce this years (13th year) tournament a bit differently.

* Poster should grab the players (brief outline)
* Flyer should have more detail and graphics
* Design flows in each Poster/Flyer.

There are several components to the Tournament that include:

1. Tournament Logo
2. Prizes (Set of golf clubs and Hotel Accommodation)
3. FairwayLogix App (Live leaderboard)
4. Timetable of events and golf
5. Venue of Golf Tournament
6. Payment terms

All information relating to components are attached.

1. Tournament Logo - Some brief background, The "Torvenne" was religious compass like symbol that basically pointed the people in the right direction when they were being faithful. We have incorporated the Logo with a golf tournament :-).

2. 1st Prize - full set of Fitted Harrier ZEN Flux Max Golf Clubs with ZEN Golf Bag (Worth $2, 200 RRP)

2nd Prize - 2 nights 5 Star Accommodation at any Brenmore Hotel in Australia includes Breakfast. (Worth $700 RRP).

Fairway Logix is a free mobile Golf app that will take the Torvenne Classic to another level.

Easy mobile live scoring, leaderboards, chat, stats & social interactions - all real time with all popular game formats.

Bring it On!

More info go to http://www.fairwaylogix.example/

* Can you incorporate some graphics from website in Poster and Flyer.

4. Timetable document attached. Make it presentable on the Flyer.

5. If we can incorporate aspects (graphics) of the golf course e.g. Golf Course Logo's, signature holes etc.

Go to:

a. Tamblin Vale Course - http://www.tamblinvale.example.au
b. Mount Orrin Golf Resort - https://www.vtma.example.au/wps/wcm/connect/vtma/Resorts/VTMA+Resorts/VTMA+Mount+Orrin+Resort/Mount+Orrin+Golf

If you go to findora images I'm sure you can find further images relating to the golf course.

6. Payment terms: Can you please express the "early bird special"

Also I will need a extra poster without the "early bird special" once the time runs out.

If you have any further questions please do not hesitate to drop me an email.

* Please note - I will end Project early if I find a design I desire.
Updates

Please add "like us on chatterbook" logo (see attached)

chatterbook link is - http://www.chatterbook.example/Torvenneclassic

```html
<!DOCTYPE html>
<html lang="en">
<head>
<meta charset="utf-8">
<title>Torvenne Classic Golf Tournament</title>
<link rel="stylesheet" href="https://fonts.googleapis.com/css2?family=Montserrat:wght@600;700;800&family=Questrial&display=swap">
<style>
  :root {
    --ink: #4a4d50;
    --green: #2f6a2e;
    --money: #3f8f2a;
    --banner: #4d5053;
    --white: #ffffff;
    --ball-shade: #cfd3d2;
    --gold: #b8923a;
    --brand-blue: #1d2f8c;
    --sky: #6da6dc;
    --grass: #3f9a2a;
  }
  * { margin: 0; padding: 0; box-sizing: border-box; }
  html, body { width: 848px; height: 1200px; overflow: hidden; background: var(--white); }
  .flyer {
    position: relative; width: 848px; height: 1200px; overflow: hidden;
    background: var(--white);
    font-family: "Questrial", sans-serif; color: var(--ink);
  }
  .course-photo {
    position: absolute; left: 420px; top: 0; width: 428px; height: 1200px;
    background: linear-gradient(180deg, var(--sky) 0%, #a9cbe8 14%, #4f7d2e 22%, #3b7a22 32%, var(--grass) 40%, #c9a77e 45%, #5fae2c 52%, #c2a07a 60%, #4d9a24 72%, #2f7a1a 100%);
  }
  .big-ball { position: absolute; left: 0; top: 0; }
  .event-mark {
    position: absolute; left: 520px; top: 40px; width: 300px; text-align: center;
  }
  .event-mark__dot {
    width: 78px; height: 78px; margin: 0 auto 18px;
    border-radius: 50%; background: #d9d9d6; border: 4px solid var(--gold);
  }
  .event-mark__name {
    font-family: "Questrial", sans-serif; color: var(--gold);
    font-size: 26px; letter-spacing: 2px; line-height: 1.2;
  }
  .bubble {
    position: absolute; border-radius: 50%;
    background: radial-gradient(circle at 40% 35%, #ffffff 0%, #f1f2f1 55%, var(--ball-shade) 100%);
    box-shadow: 0 2px 6px rgba(0,0,0,0.18);
  }
  .bubble--year { left: -32px; top: 70px; width: 180px; height: 180px; }
  .bubble--price { left: -30px; top: 318px; width: 184px; height: 184px; }
  .bubble--app { left: -30px; top: 562px; width: 184px; height: 184px; }
  .bubble__label {
    position: absolute; left: 14px; line-height: 0.95; font-size: 44px;
  }
  .light { font-family: "Questrial", sans-serif; }
  .heavy { font-family: "Montserrat", sans-serif; font-weight: 700; }
  .is-green { color: var(--green); }
  .is-ink { color: var(--ink); }
  .headline { position: absolute; line-height: 1; }
  .tournament-title { left: 185px; top: 110px; }
  .tournament-title .golf { display: block; margin-left: 58px; font-size: 28px; }
  .tournament-title .word { display: block; font-size: 30px; margin-top: 2px; }
  .early-bird {
    position: absolute; left: 198px; top: 292px; width: 238px; height: 37px;
    background: var(--banner); border-top: 5px solid #d7d8d8;
    color: var(--white); font-family: "Montserrat", sans-serif; font-size: 17px;
    text-align: center; line-height: 32px;
  }
  .early-bird b { font-weight: 800; }
  .early-bird span { font-weight: 600; }
  .terms {
    position: absolute; left: 200px; top: 338px; width: 280px;
    font-size: 12px; line-height: 23.5px; color: var(--ink);
  }
  .terms .money { color: var(--money); font-size: 14px; }
  .terms .tag { color: var(--green); }
  .terms .note { color: var(--green); padding-left: 6px; }
  .app-title { left: 188px; top: 628px; text-align: center; width: 246px; }
  .app-title .a { display: block; font-size: 42px; color: var(--ink); }
  .app-title .b { display: block; font-size: 42px; color: var(--green); }
  .app-title .url { display: block; font-family: "Montserrat", sans-serif; font-weight: 600; font-size: 15px; color: var(--green); }
  .prize-photo {
    position: absolute; left: 196px; top: 745px; width: 188px; height: 188px; border-radius: 50%;
    border: 4px solid #d8d9d8;
    background: radial-gradient(circle at 50% 45%, #e9ecef 0%, #2c54a8 45%, #1e2430 75%, #d46a2a 100%);
  }
  .first-prize { left: 19px; top: 824px; }
  .first-prize .place { display: block; font-size: 26px; color: var(--green); }
  .first-prize .what { display: block; font-size: 31px; color: var(--ink); letter-spacing: -0.5px; }
  .first-prize .small { display: block; font-size: 8.5px; color: var(--ink); margin-top: 2px; }
  .hotel-badge {
    position: absolute; left: 26px; top: 948px; width: 150px; height: 150px; border-radius: 50%;
    background: var(--white); border: 4px solid #c9cbcb;
    display: flex; align-items: center; justify-content: center;
    font-family: "Questrial", sans-serif; font-size: 26px; color: var(--brand-blue);
  }
  .second-prize { left: 188px; top: 996px; }
  .second-prize .place { display: block; font-size: 26px; color: var(--green); }
  .second-prize .what { display: block; font-size: 31px; color: var(--ink); }
  .second-prize .small { display: block; font-size: 9px; color: var(--ink); margin-left: 10px; }
  .contact { position: absolute; left: 52px; top: 1144px; font-size: 12px; color: var(--ink); }
  .contact__phone { display: flex; align-items: center; gap: 6px; margin-top: 6px; margin-left: 14px; font-family: "Montserrat", sans-serif; font-weight: 700; font-size: 13px; }
  .connectors { position: absolute; left: 0; top: 0; pointer-events: none; }
</style>
</head>
<body>
<main class="flyer">
  <div class="course-photo" role="img" aria-label="Golf course photograph: blue sky, trees, green fairway, flag on the green and a golfer playing out of a sand bunker"></div>

  <svg class="big-ball" width="848" height="1200" viewBox="0 0 848 1200" role="img" aria-label="Giant dimpled golf ball curving across the page">
    <defs>
      <radialGradient id="ballShade" cx="-587" cy="603" r="1185" gradientUnits="userSpaceOnUse">
        <stop offset="0.80" stop-color="#ffffff"/>
        <stop offset="0.93" stop-color="#f0f1f0"/>
        <stop offset="1" stop-color="#bfc4c3"/>
      </radialGradient>
    </defs>
    <circle cx="-587" cy="603" r="1185" fill="url(#ballShade)"/>
  </svg>

  <div class="event-mark">
    <div class="event-mark__dot"></div>
    <div class="event-mark__name">THE TORVENNE<br>CLASSIC</div>
  </div>

  <svg class="connectors" width="848" height="1200" viewBox="0 0 848 1200" fill="none" stroke="#8e9292" stroke-width="1.6" stroke-dasharray="8 6">
    <path d="M150 190 C 160 230, 190 250, 165 290"/>
    <path d="M172 492 C 190 540, 185 590, 160 628"/>
    <path d="M154 622 l 6 8 l 4 -10" stroke-dasharray="none"/>
    <path d="M170 700 C 195 710, 210 730, 220 752"/>
    <path d="M214 746 l 6 8 l 2 -10" stroke-dasharray="none"/>
    <path d="M196 880 C 170 900, 150 925, 142 955"/>
    <path d="M137 946 l 5 10 l 6 -9" stroke-dasharray="none"/>
  </svg>

  <div class="bubble bubble--year">
    <div class="bubble__label" style="top:52px;left:40px">
      <span class="heavy is-ink" style="display:block;font-size:38px">13th</span>
      <span class="light is-green" style="display:block;font-size:42px">YEAR</span>
    </div>
  </div>
  <div class="headline tournament-title">
    <span class="golf heavy is-green">GOLF</span>
    <span class="word light is-ink">TOURNAMENT</span>
  </div>

  <div class="bubble bubble--price">
    <div class="bubble__label" style="top:52px;left:46px">
      <span class="light is-green" style="display:block;font-size:40px">ONLY</span>
      <span class="heavy is-ink" style="display:block;font-size:40px">595<span style="font-size:24px">$</span></span>
    </div>
  </div>
  <div class="early-bird"><b>EARLY</b> <span>BIRD</span> <b>PRICE</b></div>
  <p class="terms">
    <span class="tag">a)</span>Get a <span class="money">$65</span> savings when you pay the total of <span class="money">$530</span> upfront before 15th July 2013 .<br>
    <span class="tag">b)</span>or Pay <span class="money">$300</span> before the 30th June to secure your place. The remaining <span class="money">$295</span> to be paid before the 30th Sept.<br>
    <span class="note">•&nbsp; Due to individual cancellations we can only refund money if someone replaces your spot.</span>
  </p>

  <div class="bubble bubble--app">
    <div class="bubble__label" style="top:50px;left:48px">
      <span class="light is-green" style="display:block;font-size:42px">MOB</span>
      <span class="heavy is-ink" style="display:block;font-size:42px">APP</span>
    </div>
  </div>
  <div class="headline app-title">
    <span class="a heavy">FAIRWAY</span>
    <span class="b light">LOGIX</span>
    <span class="url">www.fairwaylogix.example</span>
  </div>

  <div class="prize-photo" role="img" aria-label="Photograph of golf bags in blue, black, white and orange"></div>
  <div class="headline first-prize">
    <span class="place light">1ST PLACE</span>
    <span class="what heavy">FULL SET</span>
    <span class="small light">Fitted Harrier ZEN Flux Max Golf Clubs</span>
  </div>

  <div class="hotel-badge">Brenmore</div>
  <div class="headline second-prize">
    <span class="place light">2ND PLACE</span>
    <span class="what heavy">5* HOTEL</span>
    <span class="small light">INCLUDING BREAKFAST</span>
  </div>

  <div class="contact">
    Contact Dario if any questions
    <div class="contact__phone">
      <svg width="18" height="20" viewBox="0 0 18 20" aria-hidden="true">
        <rect width="18" height="20" rx="3" fill="#2f6a2e"/>
        <path d="M5 4c1 0 2 2 2 3s-1 1-1 2 2 4 3 4 1-1 2-1 3 1 3 2-1 2-2 2C7 16 3 11 3 6c0-1 1-2 2-2z" fill="#fff"/>
      </svg>
      0400 555 182
    </div>
  </div>
</main>
</body>
</html>
```